Website Design Project for Beauty & Wellness Professionals

As background information, I have a website that is focused on Beauty & Wellness Professionals:
- Job Search (www.lumarinovo.com)
- Business Classifieds (negocios.lumarinovo.com)
- Freelancer Classifieds (freelancer.lumarinovo.com)
- Course Reviews (cursos.lumarinovo.com)

All those websites use standard templates.

I need a DESIGN for the HOME PAGE (no coding) of the Website Platform that consolidates the four platforms under the same design.

Website designs that we like:
- quelvox.com
- brintmoor.com

Target Market(s)

Brazilian Professionals from Beauty & Wellness sector

Industry/Entity Type

Business

Requirements
Must have
• Website designs that we like:
- quelvox.com
- brintmoor.com

```html
<!DOCTYPE html>
<html lang="pt-BR">
<head>
<meta charset="utf-8">
<title>Lumarinovo – Beauty &amp; Wellness Careers</title>
<link href="https://fonts.googleapis.com/css2?family=Source+Sans+3:wght@400;600;700&display=swap" rel="stylesheet">
<style>
:root{
  --sky:#7cc3dc;
  --orange:#d9825a;
  --orange-text:#e07a4a;
  --orange-btn:#f06a22;
  --red:#e0484a;
  --green:#2eaa5c;
  --footer:#7db87a;
  --ink:#4a4a4a;
  --muted:#777;
  --line:#e2e2e2;
  --row:#f4f4f4;
  --white:#fff;
}
*{box-sizing:border-box;margin:0;padding:0}
html,body{width:1200px;height:2198px;overflow:hidden}
body{position:relative;background:var(--white);font-family:"Source Sans 3",sans-serif;color:var(--ink)}
.abs{position:absolute}

/* top bar */
.topbar{left:0;top:0;width:1200px;height:49px;background:var(--sky);color:#fff;font-size:15px}
.topbar .links{position:absolute;right:88px;top:15px;display:flex;gap:18px}
.topbar .sep{opacity:.7}

/* header */
.brand{left:88px;top:64px;display:flex;flex-direction:column;align-items:center;gap:8px}
.brand .mark{width:44px;height:44px;border-radius:50%;background:var(--orange)}
.brand .name{color:#3f9fc4;font-size:26px;font-weight:400}
.nav{right:88px;top:110px;display:flex;gap:25px;font-size:15px;color:#333}
.nav .active{color:var(--orange-text)}

/* hero */
.hero{left:0;top:177px;width:1200px;height:545px;background:linear-gradient(90deg,#3a2a24 0%,#8a6a5c 35%,#d4aa98 60%,#c8978a 85%,#6a4a40 100%)}
.hero-title{left:264px;top:416px;color:#fff;font-size:26px}
.search-box{left:253px;top:458px;width:535px;height:64px;background:rgba(255,255,255,.25)}
.search-input{left:260px;top:467px;width:385px;height:46px;background:#fff;font-size:14px;font-style:italic;color:#888;padding:14px 18px}
.search-btn{left:660px;top:467px;width:115px;height:46px;background:var(--sky);color:#fff;font-size:24px;text-align:center;line-height:46px}
.dots{left:1062px;top:692px;display:flex;gap:5px}
.dots span{width:8px;height:8px;border-radius:50%;background:#222;border:1px solid #fff}
.dots span:first-child{background:#fff}

/* jobs table */
.jobs{left:87px;top:761px;width:741px;height:677px;border:1px solid var(--line);border-radius:6px;overflow:hidden;background:#fff}
.jobs-head{height:55px;background:var(--orange);color:#fff;font-size:17px;position:relative}
.jobs-head span{position:absolute;top:17px}
.job{position:relative;height:124px;border-top:1px solid #fff}
.job:nth-child(even){background:var(--row)}
.job .thumb{position:absolute;left:9px;top:25px;width:50px;height:50px;background:#d8c8c0}
.job .title{position:absolute;left:74px;top:20px;width:220px;color:var(--orange-text);font-size:16px;font-weight:600;line-height:21px}
.job .who{position:absolute;left:74px;top:66px;width:200px;font-size:13.5px;line-height:21px;color:var(--ink)}
.job .city{position:absolute;left:328px;top:18px;color:var(--orange-text);font-size:17px}
.job .state{position:absolute;left:328px;top:42px;width:150px;font-size:13.5px;line-height:21px}
.job .date{position:absolute;left:506px;top:26px;font-size:13.5px;line-height:21px}
.job .tag{position:absolute;left:590px;top:35px;width:130px;height:28px;color:#fff;font-size:14px;text-align:center;line-height:28px;border-radius:2px}
.tag.clt{background:var(--red)}
.tag.auto{background:var(--green)}

/* sidebar */
.side-title{color:var(--orange-text);font-size:20px}
.vac-list{left:879px;top:808px;list-style:none;font-size:13.5px;color:#555}
.vac-list li{height:29px;padding-left:17px;position:relative}
.vac-list li::before{content:"›";position:absolute;left:0;top:-2px;font-size:16px;color:#888}
.tabs{left:877px;top:1128px;display:flex;gap:14px;font-size:14px}
.tabs span{background:#e8e8e8;padding:8px 16px;height:38px}
.tag-list{left:877px;top:1166px;width:236px}
.tag-list div{height:48px;background:#f2f2f2;border-bottom:2px solid #fff;font-size:14px;color:#555;padding:14px 17px;position:relative}
.tag-list div::after{content:"›";position:absolute;right:12px;top:11px;color:#999;font-size:16px}
.sponsor{left:877px;top:1435px;width:236px;height:268px;border:1px solid #ccc;background:linear-gradient(180deg,#f4f4f4,#e4dcd6)}
.sponsor .name{position:absolute;right:14px;top:20px;font-size:18px;color:#444}
.sponsor .strip{position:absolute;left:0;bottom:0;width:100%;height:22px;background:#333;color:#fff;font-size:11px;padding:4px 6px}
.sponsor .strip b{position:absolute;right:6px;top:4px;background:var(--orange-btn);font-size:9px;padding:0 4px}
.newsletter{left:877px;top:1740px;width:236px;height:171px;border:1px solid var(--line);padding:10px 12px}
.newsletter h3{font-weight:400;color:var(--orange-text);font-size:20px}
.newsletter p{font-size:13.5px;line-height:21px;color:#666;margin-top:6px}
.newsletter .field{border:1px solid #ddd;height:28px;font-size:12px;color:#999;padding:5px 8px;margin-top:8px}
.newsletter .sub{position:absolute;right:16px;bottom:22px;background:var(--orange);color:#fff;font-size:14px;padding:3px 8px}

/* courses */
.courses-title{left:120px;top:1466px}
.course{top:1512px;width:314px;height:306px;border:1px solid #ddd;background:#fff}
.course .photo{position:absolute;left:6px;top:6px;width:300px;height:176px}
.course .cap{position:absolute;left:6px;top:150px;width:300px;height:32px;background:rgba(0,0,0,.6);color:#fff;font-size:18px;padding:5px 13px;letter-spacing:-.3px}
.course p{position:absolute;left:18px;top:191px;width:282px;font-size:12.5px;line-height:14px;color:#222}
.course p em{font-style:normal;color:var(--orange-btn)}
.course .try{position:absolute;left:20px;top:260px;width:157px;height:30px;background:var(--orange-btn);color:#fff;font-size:12.5px;font-weight:700;text-align:center;line-height:30px}
.course .partner{position:absolute;right:18px;top:265px;font-size:19px;color:#444;display:flex;align-items:center;gap:4px}
.course .partner i{width:20px;height:20px;background:var(--orange-btn);display:inline-block}
.promo{left:121px;top:1848px;width:674px;height:60px;background:linear-gradient(90deg,#3fa6d8,#6ec8ea 60%,#3a9fd0);display:flex;align-items:center;justify-content:center}
.promo span{color:#1f5a1a;font-weight:700;font-size:23px;line-height:25px;text-align:center}

/* footer */
.footer{left:0;top:1962px;width:1200px;height:236px;background:var(--footer);color:#fff}
.fcol{position:absolute;top:20px}
.fcol h4{font-weight:400;font-size:18px;margin-bottom:8px}
.fcol li{list-style:none;font-size:13.5px;line-height:21.5px}
.fbrand{position:absolute;left:685px;top:22px;width:330px;text-align:center}
.fbrand .mark{width:44px;height:44px;border-radius:50%;background:#fff;opacity:.9;margin:0 auto 6px}
.fbrand .name{font-size:22px}
.fbrand p{font-size:13.5px;line-height:21.5px;margin-top:10px}
.social{position:absolute;left:338px;top:174px;display:flex;gap:8px}
.social span{width:28px;height:28px;border-radius:50%;background:rgba(255,255,255,.35)}
.fnote{position:absolute;right:30px;top:184px;font-size:12px}
</style>
</head>
<body>

<div class="abs topbar"><div class="links"><span>Advertise Job Vacancy</span><span class="sep">¦</span><span>Log in / Register</span></div></div>

<div class="abs brand"><div class="mark"></div><div class="name">Lumarinovo</div></div>
<nav class="abs nav"><span class="active">Home</span><span>Blog</span><span>For Professionals</span><span>For Business</span><span>Events &amp; Partners</span><span>About us</span><span>Contact us</span></nav>

<div class="abs hero" role="img" aria-label="Close-up photo of a makeup artist applying powder with a brush"></div>
<div class="abs hero-title">Search for a job here</div>
<div class="abs search-box"></div>
<div class="abs search-input">Search for a job here..</div>
<div class="abs search-btn">SEARCH</div>
<div class="abs dots"><span></span><span></span><span></span><span></span></div>

<section class="abs jobs">
  <div class="jobs-head"><span style="left:14px">Job Name</span><span style="left:328px">Location</span><span style="left:506px">Date</span></div>
  <div class="job"><div class="thumb" role="img" aria-label="Salon photo"></div><div class="title">Aux. Hairdresser (Escovista) - Santo André (SP)</div><div class="who">Marta Quevedo / Oriel Hair and Esthetics</div><div class="city">Santo André</div><div class="state">São Paulo, the Federative Republic of Brazil</div><div class="date">July 18,<br>2013</div><div class="tag clt">Registered (CLT)</div></div>
  <div class="job"><div class="thumb" role="img" aria-label="Salon photo"></div><div class="title">Aux. Hairdresser (Escovista) - Santo André (SP)</div><div class="who">Marta Quevedo / Oriel Hair and Esthetics</div><div class="city">Santo André</div><div class="state">São Paulo, the Federative Republic of Brazil</div><div class="date">July 18,<br>2013</div><div class="tag auto">Autonomous</div></div>
  <div class="job"><div class="thumb" style="background:#e8d88a" role="img" aria-label="Company badge"></div><div class="title">Aux. Hairdresser (Escovista) - Santo André (SP)</div><div class="who">Marta Quevedo / Oriel Hair and Esthetics</div><div class="city">Santo André</div><div class="state">São Paulo, the Federative Republic of Brazil</div><div class="date">July 18,<br>2013</div><div class="tag clt">Registered (CLT)</div></div>
  <div class="job"><div class="thumb" style="background:#e6b8c0" role="img" aria-label="Company badge"></div><div class="title">Aux. Hairdresser (Escovista) - Santo André (SP)</div><div class="who">Marta Quevedo / Oriel Hair and Esthetics</div><div class="city">Santo André</div><div class="state">São Paulo, the Federative Republic of Brazil</div><div class="date">July 18,<br>2013</div><div class="tag auto">Autonomous</div></div>
  <div class="job"><div class="thumb" style="background:#c8dce8" role="img" aria-label="Company badge"></div><div class="title">Aux. Hairdresser (Escovista) - Santo André (SP)</div><div class="who">Marta Quevedo / Oriel Hair and Esthetics</div><div class="city">Santo André</div><div class="state">São Paulo, the Federative Republic of Brazil</div><div class="date">July 18,<br>2013</div><div class="tag clt">Registered (CLT)</div></div>
</section>

<h3 class="abs side-title" style="left:877px;top:768px;font-weight:400">Job Vacancies</h3>
<ul class="abs vac-list">
  <li>Mauris fermen cosectetur adipiscing</li><li>Tumdid cosectetur adipiscing</li><li>Uam cosectetur adipiscing</li><li>leotumdium cosectetur</li><li>Sed oreet aliquam</li><li>leo Ut tellus dolor</li><li>Uam cosectetur adipiscing</li><li>leotumdium cosectetur</li><li>Sed oreet aliquam</li><li>leo Ut tellus dolor</li>
</ul>
<div class="abs tabs"><span>Search by</span><span>Tags</span></div>
<div class="abs tag-list"><div>Uam cosectetur adipiscing</div><div>leotumdium cosectetur</div><div>Sed oreet aliquam</div><div>leo Ut tellus dolor</div></div>

<h3 class="abs side-title" style="left:877px;top:1391px;font-weight:400">Sponsers</h3>
<div class="abs sponsor" role="img" aria-label="Sponsor advert showing furniture and kitchen products"><span class="name">Tavolo Casa</span><div class="strip">Your online home store<b>SHOP NOW</b></div></div>

<div class="abs newsletter"><h3>Newsletter Signup</h3><p>Enter your email address subscribe and receive notifications.</p><div class="field">Enter Email Address</div><span class="sub">SUBSCRIBE</span></div>

<h3 class="abs side-title courses-title" style="font-weight:400">Online Courses Cursivo</h3>
<div class="abs course" style="left:121px"><div class="photo" style="background:linear-gradient(135deg,#c9c9c9,#8a8a8a 55%,#d8b8a0)" role="img" aria-label="Hairdresser cutting hair with scissors"></div><div class="cap">Curso de <b>Cabeleireiro Profissional</b></div><p>Seja um profissional <b>mais qualificado</b>, invista na sua carreira e se prepare para o mercado de trabalho. <b>Matricule-se agora</b> no curso Cursivo de <em>Cabeleireiro Profissional</em>.</p><div class="try">EXPERIMENTE GRÁTIS</div><div class="partner">Cursivo<i></i></div></div>
<div class="abs course" style="left:481px"><div class="photo" style="background:linear-gradient(135deg,#6a4a68,#b58aa8 50%,#4a3448)" role="img" aria-label="Makeup brush over loose powder"></div><div class="cap">Curso de <b>Maquiagem Profissional</b></div><p>Seja um profissional <b>mais qualificado</b>, invista na sua carreira e se prepare para o mercado de trabalho. <b>Matricule-se agora</b> no curso Cursivo de <em>Maquiagem Profissional</em>.</p><div class="try">EXPERIMENTE GRÁTIS</div><div class="partner">Cursivo<i></i></div></div>

<div class="abs promo" role="img" aria-label="Banner with beauty professionals"><span>Espaço para Empresas e Profissionais de<br>Beleza, Estética e Bem-estar</span></div>

<footer class="abs footer">
  <div class="fcol" style="left:86px"><h4>Beauty</h4><ul><li>Aux Hairdresser</li><li>Aux Escovista</li><li>Hairdresser</li><li>epilator</li><li>Manicure</li><li>Makeup</li><li>Eyebrow Designer</li></ul></div>
  <div class="fcol" style="left:259px"><h4>Health and Wellness</h4><ul><li>Esthetician</li><li>Massage Therapis</li><li>Podiatrist</li><li>Physiotherapist</li><li>Nurse</li></ul></div>
  <div class="fcol" style="left:477px"><h4>Sales and Admi</h4><ul><li>Reception</li><li>Sale Cosmetics</li><li>Auxiliary Cleaning</li><li>Management</li></ul></div>
  <div class="fbrand"><div class="mark"></div><div class="name">Lumarinovo</div><p>Copyright 2013 @ Lumarinovo - Your Community for Professionals and Companies Beauty, Aesthetics and Wellness</p></div>
  <div class="social"><span></span><span></span><span></span><span></span></div>
  <div class="fnote">X4</div>
</footer>

</body>
</html>
```